Design bcard for Valtrove Consulting and Training LLC

I need a logo inspired by the term Valtrove. I'd like to have type of work I do on the back side, i.e. provide V and T on DEIJ, SDOH,...... Front of card--business name, contact information, and possibly a tag line.

Target Market(s)

NGOs, human service agencies, education, healthcare, public health.

Contact Information for Business Card

Name of business, email address, phone number, logo--on front. Services on the back

Font styles to use
Sans Serif

Requirements
Must have
• Contact information, creative logo, services

```html
<!DOCTYPE html>
<html lang="en">
<head>
<meta charset="utf-8">
<title>Valtrove Consulting and Training LLC – Business Card</title>
<link href="https://fonts.googleapis.com/css2?family=Lato:wght@400;700;900&display=swap" rel="stylesheet">
<style>
  :root {
    --bg: #3a3a3a;
    --purple: #865ca8;
    --blue: #1b7bc2;
    --ink: #333333;
    --white: #ffffff;
  }
  * { margin: 0; padding: 0; box-sizing: border-box; }
  html, body { width: 1200px; height: 689px; overflow: hidden; }
  body {
    background: var(--bg);
    font-family: "Lato", sans-serif;
    position: relative;
  }
  .card {
    position: absolute;
    top: 190px;
    width: 540px;
    height: 309px;
    border-radius: 18px;
    overflow: hidden;
  }
  /* Back side */
  .card--back { left: 40px; background: var(--purple); color: var(--white); }
  .brand {
    position: absolute;
    display: flex;
    align-items: center;
    gap: 10px;
    font-weight: 900;
    letter-spacing: 1px;
  }
  .brand__dot { border-radius: 50%; flex: none; }
  .card--back .brand { left: 0; right: 0; top: 80px; justify-content: center; font-size: 58px; }
  .card--back .brand__dot { width: 22px; height: 22px; background: var(--white); }
  .services {
    position: absolute;
    left: 20px; right: 20px; top: 210px;
    text-align: center;
    font-size: 12.5px;
    line-height: 1.7;
  }
  /* Front side */
  .card--front { left: 620px; background: var(--white); color: var(--ink); }
  .card--front .brand { right: 30px; top: 26px; font-size: 36px; color: var(--blue); }
  .card--front .brand__dot { width: 14px; height: 14px; background: var(--purple); }
  .divider { position: absolute; height: 1px; background: var(--blue); }
  .divider--top { left: 30px; right: 30px; top: 88px; }
  .person { position: absolute; left: 30px; top: 104px; }
  .person__name { font-size: 26px; font-weight: 900; color: var(--blue); letter-spacing: .5px; }
  .person__role { font-size: 15px; color: var(--purple); margin-top: 2px; }
  .divider--contact { left: 30px; width: 220px; top: 170px; }
  .contacts { position: absolute; left: 30px; top: 180px; list-style: none; font-size: 12.5px; line-height: 21px; }
  .contacts li { display: flex; align-items: center; gap: 10px; }
  .contacts svg { width: 12px; height: 12px; fill: var(--purple); flex: none; }
  .office { position: absolute; right: 30px; top: 104px; text-align: right; font-size: 12.5px; line-height: 20px; }
  .office__name { font-weight: 900; color: var(--purple); font-size: 13px; }
  .band { position: absolute; left: 0; right: 0; bottom: 0; height: 44px; }
  .band svg { position: absolute; inset: 0; width: 100%; height: 100%; }
  .band__tagline {
    position: absolute; left: 30px; top: 0; line-height: 44px;
    color: var(--white); font-size: 13px; letter-spacing: 1px; text-transform: uppercase;
  }
</style>
</head>
<body>
  <section class="card card--back" aria-label="Card back">
    <div class="brand"><span class="brand__dot"></span><span>VALTROVE</span></div>
    <p class="services">
      Health Care &amp; Quality | Neighborhood &amp; Built Environment | Economic Stability<br>
      Social and Community Context | Education Access and Quality
    </p>
  </section>

  <section class="card card--front" aria-label="Card front">
    <div class="brand"><span class="brand__dot"></span><span>VALTROVE</span></div>
    <div class="divider divider--top"></div>

    <div class="person">
      <h1 class="person__name">DANA WHITFIELD</h1>
      <p class="person__role">Founder &amp; CEO</p>
    </div>
    <div class="divider divider--contact"></div>
    <ul class="contacts">
      <li><svg viewBox="0 0 12 12"><path d="M2.5 1l2 2-1 1.5a7 7 0 0 0 4 4l1.5-1 2 2-1.5 1.5C5 11 1 7 1 2.5z"/></svg>(555) 218-4470</li>
      <li><svg viewBox="0 0 12 12"><path d="M3 0h6a1 1 0 0 1 1 1v10a1 1 0 0 1-1 1H3a1 1 0 0 1-1-1V1a1 1 0 0 1 1-1zm0 1.5v7.5h6V1.5z"/></svg>(555) 362-9015</li>
      <li><svg viewBox="0 0 12 12"><path d="M3 0h6v3H3zM1 4h10v5H9v3H3V9H1zm3 4v3h4V8z"/></svg>(555) 731-5528</li>
      <li><svg viewBox="0 0 12 12"><path d="M0 2h12v1L6 7 0 3zm0 2.5l6 4 6-4V10H0z"/></svg>hello@valtrove-ct.com</li>
    </ul>

    <address class="office" style="font-style:normal">
      <p class="office__name">Valtrove Consulting &amp; Training LLC</p>
      <p>418 Linden Hollow Road, Ste 7</p>
      <p>Brookmere, CT 06999</p>
      <p>www.valtrove-ct.com</p>
    </address>

    <div class="band">
      <svg viewBox="0 0 540 44" preserveAspectRatio="none" aria-hidden="true">
        <polygon points="0,0 420,0 410,44 0,44" fill="#1b7bc2"/>
        <polygon points="426,0 540,0 540,44 416,44" fill="#865ca8"/>
      </svg>
      <p class="band__tagline">Your tagline goes here</p>
    </div>
  </section>
</body>
</html>
```